Vantor Ridge needs a Business Card Design

We need a business card design for an Information Technology company based in Fairfax Virginia called Vantor Ridge. We want the business card to use our logo colors. We need it to be double-sided. The business card needs to look professional but we would like it to be unique. You can get company information from our web site (http://www.vantorridgellc.example).

Target Market(s)

Target market is Government Agencies and Business Professionals.

Industry/Entity Type

Business

Requirements
Must have
• Must have section for company name, company address, company URL, employee name, title, phone and email. Also must have company logo and space for entering logos.

```html
<!DOCTYPE html>
<html lang="en">
<head>
<meta charset="utf-8">
<title>Vantor Ridge Business Card</title>
<link href="https://fonts.googleapis.com/css2?family=Oswald:wght@500&family=Open+Sans:wght@400;600;700&display=swap" rel="stylesheet">
<style>
  :root {
    --stage: #9aabb0;
    --card-white: #ffffff;
    --brand-blue: #283a93;
    --accent-blue: #1a73c4;
    --name-blue: #1f5fb3;
    --text-grey: #6b6b6b;
    --icon-grey: #7a7a7a;
    --rule-red: #d9423a;
  }
  * { margin: 0; padding: 0; box-sizing: border-box; }
  html, body { width: 1200px; height: 960px; overflow: hidden; }
  body {
    background: var(--stage);
    font-family: "Open Sans", Arial, sans-serif;
    position: relative;
  }
  .card {
    position: absolute;
    left: 280px;
    width: 640px;
    height: 366px;
    border-radius: 4px;
    box-shadow: 0 10px 28px rgba(0,0,0,0.25);
    overflow: hidden;
  }
  /* Front */
  .card--front { top: 80px; background: var(--card-white); }
  .brand {
    position: absolute;
    display: flex;
    align-items: center;
    gap: 12px;
  }
  .card--front .brand { top: 30px; right: 34px; }
  .brand__square { width: 34px; height: 34px; background: var(--brand-blue); }
  .brand__name { font-weight: 700; font-size: 30px; color: var(--brand-blue); letter-spacing: 0.5px; }
  .name-bar {
    position: absolute; left: 0; top: 196px;
    width: 80px; height: 28px; background: var(--brand-blue);
  }
  .holder {
    position: absolute; left: 92px; top: 186px; width: 300px; text-align: right;
  }
  .holder__name {
    font-family: "Oswald", "Arial Narrow", sans-serif;
    font-size: 34px; line-height: 40px; color: var(--name-blue); letter-spacing: 0.5px;
    text-transform: uppercase;
  }
  .holder__title { font-size: 16px; color: var(--text-grey); margin-top: 2px; }
  .contact {
    position: absolute; left: 408px; top: 150px;
    border-left: 2px solid var(--rule-red);
    padding: 4px 0 6px 14px;
    list-style: none;
  }
  .contact__item {
    display: flex; align-items: flex-start; gap: 10px;
    font-size: 13px; line-height: 18px; color: var(--text-grey);
    margin-bottom: 12px;
  }
  .contact__item:last-child { margin-bottom: 0; }
  .contact__item svg { flex: 0 0 16px; width: 16px; height: 16px; fill: var(--icon-grey); margin-top: 1px; }
  /* Back */
  .card--back { top: 510px; background: var(--brand-blue); }
  .card--back .brand { left: 0; right: 0; top: 130px; justify-content: center; gap: 18px; }
  .card--back .brand__square { width: 52px; height: 52px; background: var(--card-white); }
  .card--back .brand__name { font-size: 46px; color: var(--card-white); }
  .url-band {
    position: absolute; left: 180px; right: 0; bottom: 0; height: 52px;
    background: var(--accent-blue);
    border-radius: 10px 0 0 0;
    display: flex; align-items: center; justify-content: center;
    color: var(--card-white); font-size: 17px; font-weight: 600; letter-spacing: 0.5px;
  }
</style>
</head>
<body>

<section class="card card--front" aria-label="Business card front">
  <div class="brand">
    <span class="brand__square"></span>
    <span class="brand__name">Vantor Ridge</span>
  </div>

  <div class="name-bar"></div>
  <div class="holder">
    <div class="holder__name">Daniel Marsh</div>
    <div class="holder__title">Job title</div>
  </div>

  <ul class="contact">
    <li class="contact__item">
      <svg viewBox="0 0 16 16"><circle cx="8" cy="4.5" r="3.5"/><path d="M1 16c0-4 3-6.5 7-6.5s7 2.5 7 6.5z"/></svg>
      <span>company address,<br>your detail address</span>
    </li>
    <li class="contact__item">
      <svg viewBox="0 0 16 16"><path d="M3.5 1l3 3-1.8 2c.9 2 2.4 3.5 4.3 4.4l2-1.8 3 3-1.8 2.2C6.5 13.5 2.5 9.5 1.3 3z"/></svg>
      <span>703 555 0142</span>
    </li>
    <li class="contact__item">
      <svg viewBox="0 0 16 16"><path d="M1 3h14v10H1z M1.8 3.8v.6L8 8.6l6.2-4.2v-.6z" fill-rule="evenodd"/></svg>
      <span>info@vantorridge.example</span>
    </li>
    <li class="contact__item">
      <svg viewBox="0 0 16 16"><path d="M4 13a3 3 0 010-6 4.5 4.5 0 018.6-1A3.5 3.5 0 0112.5 13z"/></svg>
      <span>company URL</span>
    </li>
  </ul>
</section>

<section class="card card--back" aria-label="Business card back">
  <div class="brand">
    <span class="brand__square"></span>
    <span class="brand__name">Vantor Ridge</span>
  </div>
  <div class="url-band">www.vantorridgellc.example</div>
</section>

</body>
</html>
```